Norrell Advisory WA Business Card

Create an interesting, eye catching and colourful two sided business card. We are a business consulting operation assisting SME's improve all areas of their business. We provide consulting services to assist SME's to create a culture of continuous improvement, making a positive difference in the business. Our tag line is Small changes, big rewards. We want to create a well recognised, innovative brand that can be continued throughout our website, social media and email correspondence.

Target Market(s)

Small to Medium Enterprise Business Owners

Industry/Entity Type

Business Consultant

Contact Information for Business Card

Name of Business: Norrell Advisory - Steady Steps Lasting Gains
Derek Holloway Ph 0407385510 Megan Holloway Ph 0407913847
Email norrelladvisorywa@mailbox-example.com
Web address TBA
FaceBook page TBA

BACKSIDE OF CARD

Providing assistance with:

• Organisation & Efficiency
• Revenue generation & Marketing
• Financial Management
• Production quality & delivery
• Systems & Process documentation
• Exit Strategy

Font styles to use
Other font styles liked:
• Calibri

Colors

Designer to choose colors to be used in the design.

Requirements
Must have
• Calibri font

```html
<!DOCTYPE html>
<html lang="en">
<head>
<meta charset="utf-8">
<title>Norrell Advisory WA Business Card</title>
<link href="https://fonts.googleapis.com/css2?family=Carlito:wght@400;700&display=swap" rel="stylesheet">
<style>
  :root {
    --backdrop: #3a3a3c;
    --card-white: #ffffff;
    --card-fade: #e9e9ea;
    --brand-blue: #2e6aad;
    --brand-red: #d6463a;
    --card-red: #c13f31;
    --card-red-dark: #9e3127;
    --ink-grey: #3d3d3d;
    --back-ink: #f3dcd7;
    --back-soft: #f7e7e3;
  }
  * { box-sizing: border-box; margin: 0; padding: 0; }
  html, body { width: 1200px; height: 900px; overflow: hidden; }
  body {
    background: var(--backdrop);
    font-family: "Carlito", "Calibri", sans-serif;
    display: flex;
    flex-direction: column;
    align-items: center;
    justify-content: center;
    gap: 40px;
  }
  .card {
    width: 700px;
    height: 400px;
    border-radius: 22px;
    position: relative;
    overflow: hidden;
    box-shadow: 0 10px 24px rgba(0,0,0,0.35);
  }

  /* Front */
  .card--front {
    background: radial-gradient(circle at 62% 62%, var(--card-white) 30%, var(--card-fade) 100%);
    padding: 40px 44px;
  }
  .front__title {
    color: var(--brand-blue);
    font-weight: 700;
    font-size: 44px;
    line-height: 1;
  }
  .front__tagline {
    color: var(--brand-red);
    font-size: 26px;
    margin-top: 4px;
  }
  .front__names {
    margin-top: 34px;
    color: var(--brand-blue);
    font-weight: 700;
    font-size: 30px;
    line-height: 1.05;
    text-transform: uppercase;
  }
  .front__contacts {
    list-style: none;
    margin-top: 26px;
    color: var(--ink-grey);
    font-size: 18px;
    line-height: 1.35;
  }
  .contact { display: flex; align-items: center; gap: 8px; }
  .contact svg { width: 13px; height: 13px; fill: var(--brand-blue); flex: none; }
  .contact__web-domain { color: var(--brand-blue); }
  .front__mark {
    position: absolute;
    right: 60px;
    top: 200px;
    display: flex;
    align-items: center;
    gap: 12px;
  }
  .front__mark-square { width: 40px; height: 40px; background: var(--brand-red); }
  .front__mark-name { color: var(--brand-blue); font-weight: 700; font-size: 30px; }

  /* Back */
  .card--back {
    background: linear-gradient(135deg, var(--card-red) 40%, var(--card-red-dark) 100%);
    padding: 44px 48px;
    color: var(--back-ink);
  }
  .back__header { display: flex; align-items: center; gap: 22px; }
  .back__mark-square { width: 74px; height: 74px; background: var(--back-soft); opacity: 0.85; flex: none; }
  .back__title { font-weight: 700; font-size: 50px; line-height: 1; }
  .back__tagline { font-size: 30px; margin-top: 4px; }
  .back__services {
    list-style: none;
    margin-top: 70px;
    font-size: 22px;
    line-height: 1.3;
  }
</style>
</head>
<body>
  <section class="card card--front" aria-label="Business card front">
    <h1 class="front__title">Norrell Advisory</h1>
    <p class="front__tagline">Steady Steps Lasting Gains</p>
    <p class="front__names">Derek Holloway<br>Megan Holloway</p>
    <ul class="front__contacts">
      <li class="contact">
        <svg viewBox="0 0 16 16" aria-hidden="true"><path d="M4 1 6.5 4 5 6c1 2 3 4 5 5l2-1.5 3 2.5-2 3C7 14 2 9 1 3z"/></svg>
        0407385510
      </li>
      <li class="contact">
        <svg viewBox="0 0 16 16" aria-hidden="true"><path d="M4 1 6.5 4 5 6c1 2 3 4 5 5l2-1.5 3 2.5-2 3C7 14 2 9 1 3z"/></svg>
        0407913847
      </li>
      <li class="contact">
        <svg viewBox="0 0 16 16" aria-hidden="true"><path d="M1 3h14v10H1zm1.5 1.5v.4L8 9l5.5-4.1v-.4z"/></svg>
        norrelladvisorywa@mailbox-example.com
      </li>
      <li class="contact">
        <svg viewBox="0 0 16 16" aria-hidden="true"><circle cx="8" cy="8" r="7"/></svg>
        <span>www.<span class="contact__web-domain">norrelladvisorywa-example</span>.com</span>
      </li>
    </ul>
    <div class="front__mark">
      <span class="front__mark-square"></span>
      <span class="front__mark-name">Norrell Advisory</span>
    </div>
  </section>

  <section class="card card--back" aria-label="Business card back">
    <div class="back__header">
      <span class="back__mark-square"></span>
      <div>
        <h2 class="back__title">Norrell Advisory</h2>
        <p class="back__tagline">Steady Steps Lasting Gains</p>
      </div>
    </div>
    <ul class="back__services">
      <li>&gt; Organisation &amp; Efficiency &gt; Revenue generation &amp; Marketing</li>
      <li>&gt; Financial Management &gt; Production quality &amp; delivery</li>
      <li>&gt; Systems &amp; Process documentation &gt; Exit Strategy</li>
    </ul>
  </section>
</body>
</html>
```